Financial Advisor Resource Firm needs business card design

Need business card design for company in Omaha NE called Meridale Circle. We provide resources to financial advisors....workshop programs, retirement analysis, and insurance planning. I would like to see designs that use grays, greens, black, and white colors. The final design should communicate 'collaboration' and be simple yet attractive to financial planning clients. I will attached our logo and another picture of a puzzle piece coming together. I would like the incorporate the puzzle picture somehow, maybe on the back somehow, with color or just the gray scale....OR, the picture be the front of the card with 'Meridale' definition on it (see upload) and then company logo, employee name, title, address on the back (see ppt uploaded). The following disclosure needs to be included somewhere- Advisory services offered through Stonebrook Assets, LLC.
Updates

I uploaded a svg and ai file of the logo

Target Market(s)

Financial planning clients and financial advisors....so pretty diverse age range of about 40-70.

Industry/Entity Type

Financial Planning

Contact Information for Business Card

Tobias L. Fenwright, MBA
Founder/President
5287 E. Larkin Road
Suite 230
Omaha, NE 68190
Phone- (402) 555-0147
Cell- (402) 555-0183
Fax- (402) 555-0129
email- tobias@meridaleplan.example
web address- www.meridaleplan.example

Colors
1b1b1b
474747
d3d3d3
ffffff
9bcb3c
abd036

Requirements
Must have
• Must include logo provided, must be 2 sided, and must have disclosure...all of these items listed in project description

```html
<!DOCTYPE html>
<html lang="en">
<head>
<meta charset="utf-8">
<title>Meridale Circle – Business Card</title>
<link href="https://fonts.googleapis.com/css2?family=Arimo:wght@400;700&family=Cinzel:wght@400;600&display=swap" rel="stylesheet">
<style>
  :root {
    --ink: #1b1b1b;
    --charcoal: #474747;
    --mist: #d3d3d3;
    --paper: #ffffff;
    --leaf: #9bcb3c;
    --lime: #abd036;
    --stage: #ececec;
  }
  * { box-sizing: border-box; margin: 0; padding: 0; }
  html, body { width: 1200px; height: 880px; overflow: hidden; }
  body { background: var(--stage); position: relative; font-family: "Arimo", Arial, sans-serif; color: var(--ink); }

  .card {
    position: absolute;
    width: 700px; height: 400px;
    background: var(--paper);
    border-radius: 22px;
    overflow: hidden;
    box-shadow: 0 8px 24px rgba(0,0,0,.18);
  }

  /* Front */
  .card-front { left: 90px; top: 30px; }
  .front-photo {
    position: absolute; inset: 0 0 120px 0;
    background: linear-gradient(160deg, #f6f6f6 0%, #d9d9d9 35%, #bdbdbd 60%, #e2e2e2 80%, var(--paper) 100%);
  }
  .front-photo::after {
    content: ""; position: absolute; inset: 0;
    background: linear-gradient(to bottom, rgba(255,255,255,0) 55%, var(--paper) 100%);
  }
  .front-brand {
    position: absolute; left: 60px; top: 255px;
    display: flex; align-items: center; gap: 14px;
  }
  .brand-dot { width: 22px; height: 22px; border-radius: 50%; background: var(--leaf); }
  .brand-name {
    font-family: "Cinzel", Georgia, serif; font-weight: 600;
    font-size: 44px; letter-spacing: 1px; color: var(--ink);
  }
  .front-tagline {
    position: absolute; left: 60px; top: 330px;
    font-size: 17px; color: var(--ink); letter-spacing: .3px;
  }

  /* Back */
  .card-back { left: 410px; top: 450px; }
  .back-strip {
    position: absolute; left: 0; top: 0; bottom: 0; width: 105px;
    background: var(--ink);
    display: flex; align-items: center; justify-content: center;
  }
  .strip-brand {
    transform: rotate(-90deg);
    white-space: nowrap;
    display: flex; align-items: center; gap: 10px;
  }
  .strip-brand .brand-name { color: var(--paper); font-size: 30px; }
  .strip-brand .brand-dot { width: 16px; height: 16px; }

  .person { position: absolute; left: 160px; top: 190px; }
  .person-name {
    font-family: "Cinzel", Georgia, serif; font-weight: 400;
    font-size: 20px; letter-spacing: .5px; color: var(--ink);
    white-space: nowrap;
  }
  .person-title { font-size: 17px; color: var(--leaf); margin-top: 2px; }

  .contact-list { list-style: none; margin-top: 14px; }
  .contact-list li { display: flex; align-items: center; gap: 9px; font-size: 15px; line-height: 22px; color: var(--ink); }
  .contact-icon { width: 17px; height: 17px; flex: none; }

  .address {
    position: absolute; left: 478px; top: 195px;
    padding-left: 18px; border-left: 1px solid var(--mist);
    font-size: 15px; line-height: 21px; color: var(--ink);
    font-style: normal; white-space: nowrap;
  }
  .web-domain { color: var(--leaf); }

  .disclosure {
    position: absolute; left: 160px; right: 30px; bottom: 18px;
    font-size: 11px; line-height: 14px; color: var(--charcoal);
    letter-spacing: .2px;
  }
</style>
</head>
<body>

  <section class="card card-front" aria-label="Card front">
    <div class="front-photo" role="img" aria-label="Grayscale photo of two hands fitting puzzle pieces together"></div>
    <div class="front-brand">
      <span class="brand-dot"></span>
      <span class="brand-name">MERIDALE CIRCLE</span>
    </div>
    <p class="front-tagline">: to come together and unite in common interest and focus</p>
  </section>

  <section class="card card-back" aria-label="Card back">
    <div class="back-strip">
      <div class="strip-brand">
        <span class="brand-dot"></span>
        <span class="brand-name">MERIDALE CIRCLE</span>
      </div>
    </div>

    <div class="person">
      <h1 class="person-name">TOBIAS L. FENWRIGHT, MBA</h1>
      <p class="person-title">Founder/President</p>
      <ul class="contact-list">
        <li>
          <svg class="contact-icon" viewBox="0 0 20 20"><circle cx="10" cy="10" r="10" fill="var(--leaf)"/><path d="M6.5 5.5c.6-.5 1.3-.4 1.6.2l.8 1.6c.2.5 0 1-.4 1.3l-.5.4c.5 1.2 1.4 2.1 2.6 2.6l.4-.5c.3-.4.8-.6 1.3-.4l1.6.8c.6.3.7 1 .2 1.6l-.6.6c-.7.7-2 .7-3.6-.3-1.6-1-2.9-2.3-3.9-3.9-1-1.6-1-2.9-.3-3.6z" fill="#fff"/></svg>
          (402) 555-0147
        </li>
        <li>
          <svg class="contact-icon" viewBox="0 0 20 20"><circle cx="10" cy="10" r="10" fill="var(--leaf)"/><rect x="7" y="4.5" width="6" height="11" rx="1" fill="#fff"/><rect x="8" y="6" width="4" height="7" fill="var(--leaf)"/></svg>
          (402) 555-0183
        </li>
        <li>
          <svg class="contact-icon" viewBox="0 0 20 20"><circle cx="10" cy="10" r="10" fill="var(--leaf)"/><rect x="5" y="8" width="10" height="6" rx="1" fill="#fff"/><rect x="7" y="5" width="6" height="3" fill="#fff"/></svg>
          (402) 555-0129
        </li>
        <li>
          <svg class="contact-icon" viewBox="0 0 20 20"><circle cx="10" cy="10" r="10" fill="var(--leaf)"/><rect x="5" y="6.5" width="10" height="7" rx="1" fill="#fff"/><path d="M5.5 7l4.5 3.5L14.5 7" stroke="var(--leaf)" stroke-width="1.2" fill="none"/></svg>
          tobias@meridaleplan.example
        </li>
      </ul>
    </div>

    <address class="address">
      5287 E. Larkin Road<br>
      Suite 230<br>
      Omaha, NE 68190<br>
      www.<span class="web-domain">meridaleplan.example</span>
    </address>

    <p class="disclosure">Advisory services offered through Stonebrook Assets, LLC.</p>
  </section>

</body>
</html>
```